tinyTally Resource Book - 10 maths tasks to do outside

I need a 22 (11 pages back to back) page A6 sized book produced to standard for submission to professional printer. Needs to be as .pdf file showing guide lines and allowances for colour bleed. I have text already written and submitted as attachment in a Word file with margins set to A6 size. The theme of the materials is "Nature Play" so using lots of pictures from nature (Australia preferably) and showing lots of patterns in nature (rocks, leaves, flower petals etc). Some of the tasks refer to specific activities, such as "shadows" and "floating" so would be great to illustrate appropriately. The big emphasis is on learning outside the classroom, getting kids to engage actively with nature. I would like to see the pages as full colour - so not white background. The book itself will be spiral bound along the top edge so a margin of at least 1cm will be required at the top of each page (or the bottom of even numbered pages). Book will be printed on plastic laminated matte paper for outdoor use. Font size needs to be big enough to read. Fonts sizes, alignments and page numbers are all different at the moment and need to be standardised. One photo is included in a page as a sample if you can use it, otherwise disregard. Logo for Wattlebrook Numeracy Guild is also included to have as part of the acknowledgements at the back of the book.

Target Market(s)

Book is for early childhood and preschool teachers.

Industry/Entity Type

Education

Font styles to use
Sans Serif

Requirements
Must have
• Colour and appeal.
Nice to have
• Use of natural colours instead of bright catchy colours but that is your call.
Should not have
• American spelling

```html
<!DOCTYPE html>
<html lang="en-AU">
<head>
<meta charset="utf-8">
<title>tinyTally – Task 1: How Many Leaves?</title>
<link rel="stylesheet" href="https://fonts.googleapis.com/css2?family=Fredoka:wght@600&family=Questrial&display=swap">
<style>
  :root {
    --paper: #ffffff;
    --crop-mark: #3c3c3c;
    --title-green: #1d5a2b;
    --title-outline: #f4ea12;
    --bar-deep: #12a052;
    --bar-soft: #4cb253;
    --bar-text: #ffffff;
    --body-text: #3d3d3d;
    --bullet-red: #d8232a;
    --leaf-mist-1: #d3d8d6;
    --leaf-mist-2: #bcc4c1;
    --leaf-red: rgba(196, 84, 70, 0.55);
    --leaf-amber: rgba(222, 150, 70, 0.35);
  }
  * { margin: 0; padding: 0; box-sizing: border-box; }
  html, body {
    width: 892px; height: 1200px; overflow: hidden;
    background: var(--paper);
  }
  .page {
    position: relative; width: 892px; height: 1200px;
    background: var(--paper);
  }
  .crop-marks { position: absolute; inset: 0; }
  .bleed-area {
    position: absolute; left: 54px; top: 56px; width: 785px; height: 1090px;
    background:
      radial-gradient(ellipse 260px 220px at 360px 880px, var(--leaf-red), transparent 70%),
      radial-gradient(ellipse 140px 160px at 60px 960px, var(--leaf-red), transparent 70%),
      radial-gradient(ellipse 200px 180px at 200px 1010px, var(--leaf-amber), transparent 70%),
      radial-gradient(ellipse 120px 110px at 760px 200px, var(--leaf-red), transparent 70%),
      linear-gradient(165deg, var(--leaf-mist-1) 0%, var(--leaf-mist-2) 55%, var(--leaf-mist-1) 100%);
  }
  .task-title, .outcome-heading {
    position: absolute; left: 54px; width: 785px; text-align: center;
    font-family: "Fredoka", sans-serif; font-weight: 600;
    color: var(--title-green);
    -webkit-text-stroke: 5px var(--title-outline);
    paint-order: stroke fill;
  }
  .task-title { top: 108px; font-size: 52px; line-height: 60px; }
  .outcome-heading { top: 202px; font-size: 35px; line-height: 42px; }
  .section-bar {
    position: absolute; left: 124px; width: 644px;
    font-family: "Questrial", sans-serif; font-style: italic;
    color: var(--bar-text); padding-left: 2px;
  }
  .section-bar--lead { top: 364px; height: 80px; background: var(--bar-deep); font-size: 26px; line-height: 37px; padding-top: 3px; }
  .section-bar--educators { top: 544px; height: 35px; background: var(--bar-soft); font-size: 24px; line-height: 35px; }
  .section-bar--task { top: 720px; height: 35px; background: var(--bar-soft); font-size: 24px; line-height: 35px; }
  .body-copy {
    position: absolute; left: 196px; width: 580px;
    font-family: "Questrial", sans-serif; font-size: 32px; line-height: 43px;
    color: var(--body-text);
  }
  .body-copy--child { top: 443px; }
  .body-copy--educator { top: 580px; }
  .opportunity-list {
    position: absolute; left: 184px; top: 758px; width: 590px; list-style: none;
    font-family: "Questrial", sans-serif; font-size: 32px; line-height: 42px;
    color: var(--body-text);
  }
  .opportunity-list li { position: relative; padding-left: 34px; text-indent: 8px; }
  .opportunity-list li::before {
    content: ""; position: absolute; left: 4px; top: 13px;
    width: 16px; height: 16px; background: var(--bullet-red);
    transform: rotate(45deg);
  }
</style>
</head>
<body>
<div class="page">
  <div class="bleed-area" role="img" aria-label="Soft-focus photograph of falling autumn maple leaves in red and amber over a misty grey-green sky"></div>

  <svg class="crop-marks" width="892" height="1200" viewBox="0 0 892 1200" aria-hidden="true">
    <g stroke="var(--crop-mark)" stroke-width="1">
      <line x1="54" y1="0" x2="54" y2="40"/><line x1="74" y1="36" x2="74" y2="74"/>
      <line x1="0" y1="54" x2="40" y2="54"/><line x1="36" y1="74" x2="74" y2="74"/>
      <line x1="838" y1="0" x2="838" y2="40"/><line x1="818" y1="36" x2="818" y2="74"/>
      <line x1="852" y1="54" x2="892" y2="54"/><line x1="818" y1="74" x2="856" y2="74"/>
      <line x1="54" y1="1160" x2="54" y2="1200"/><line x1="74" y1="1126" x2="74" y2="1164"/>
      <line x1="0" y1="1146" x2="40" y2="1146"/><line x1="36" y1="1126" x2="74" y2="1126"/>
      <line x1="838" y1="1160" x2="838" y2="1200"/><line x1="818" y1="1126" x2="818" y2="1164"/>
      <line x1="852" y1="1146" x2="892" y2="1146"/><line x1="818" y1="1126" x2="856" y2="1126"/>
    </g>
  </svg>

  <h1 class="task-title">1. How Many Leaves?</h1>
  <h2 class="outcome-heading">EYLF – Outcome 1:<br>Children have a strong sense<br>of identity</h2>

  <p class="section-bar section-bar--lead">Children learn to interact in relation to others with care, empathy and respect when they...</p>
  <p class="body-copy body-copy--child">display awareness of and respect for others’ perspectives</p>

  <p class="section-bar section-bar--educators">Educators promote this learning when they...</p>
  <p class="body-copy body-copy--educator">organise learning environments in ways that promote small group interactions and play experiences</p>

  <p class="section-bar section-bar--task">This task provides an opportunity to:</p>
  <ul class="opportunity-list">
    <li>explore the concepts of “perspec-tive” and “comparing”</li>
    <li>attempt the same task in different ways</li>
    <li>consider relationship between the individual and the group</li>
  </ul>
</div>
</body>
</html>
```